Business card design

I already have the logo design completed and am requiring business card design and layout utilising the logo. I require a front and back design.

We are an executive recruitment company so we are looking at full colour, high finish in a reasonably conservative structure.

Reason: will be provide ai template

Target Market(s)

Senior Management 35-60 age bracket

Industry/Entity Type

Business

Requirements
Must have
• Peter Welling
• Director
• 238 Morrow Tce, Kelvin Grove QLD 4059
• Ph: 07 3628 4190 Mob: 0418527306
• peter@voltinapartners.com.au
• www.voltinapartners.com.au
Nice to have
• Ideally full colour,
Should not have
• cheap looking

```html
<!DOCTYPE html>
<html lang="en">
<head>
<meta charset="utf-8">
<title>Voltina Partners – Business Card</title>
<link rel="stylesheet" href="https://fonts.googleapis.com/css2?family=Open+Sans:wght@400;700&display=swap">
<style>
  :root {
    --page-bg: #e9ecf0;
    --navy-deep: #0d2f5c;
    --navy: #17467f;
    --navy-light: #2f6aa6;
    --brand-text: #1c3f6e;
    --grey-text: #8a8d91;
    --grey-name: #6f7276;
    --stripe-dark: #1f5fa8;
    --stripe-light: #3d8ad6;
    --white: #ffffff;
  }
  * { margin: 0; padding: 0; box-sizing: border-box; }
  html, body {
    width: 1200px;
    height: 1200px;
    overflow: hidden;
    background: var(--page-bg);
    font-family: "Open Sans", Arial, sans-serif;
  }
  .canvas {
    position: relative;
    width: 1200px;
    height: 1200px;
  }
  .card {
    position: absolute;
    left: 180px;
    width: 840px;
    height: 513px;
    overflow: hidden;
    box-shadow: 0 6px 22px rgba(20, 40, 70, 0.18);
  }

  /* Back of card */
  .card-back {
    top: 60px;
    background:
      radial-gradient(ellipse 60% 70% at 62% 40%, rgba(90, 150, 210, 0.35), transparent 70%),
      linear-gradient(135deg, var(--navy-deep) 0%, var(--navy) 55%, var(--navy-light) 100%);
    color: var(--white);
  }
  .card-back .brand {
    position: absolute;
    top: 200px;
    left: 0;
    width: 100%;
    display: flex;
    justify-content: center;
    align-items: center;
    gap: 20px;
  }
  .brand-mark {
    width: 54px;
    height: 54px;
    background: var(--white);
  }
  .card-back .brand-name {
    font-size: 46px;
    font-weight: 700;
    letter-spacing: 3px;
    color: var(--white);
  }
  .card-back .website {
    position: absolute;
    bottom: 62px;
    width: 100%;
    text-align: center;
    font-size: 27px;
    letter-spacing: 0.5px;
    color: var(--white);
  }

  /* Front of card */
  .card-front {
    top: 627px;
    background: var(--white);
  }
  .card-front .brand {
    position: absolute;
    top: 50px;
    left: 52px;
    display: flex;
    align-items: center;
    gap: 16px;
  }
  .card-front .brand-mark {
    width: 46px;
    height: 46px;
    background: var(--brand-text);
  }
  .card-front .brand-name {
    font-size: 38px;
    font-weight: 700;
    letter-spacing: 2.5px;
    color: var(--brand-text);
  }
  .holder {
    position: absolute;
    top: 150px;
    left: 52px;
  }
  .holder-name {
    font-size: 27px;
    font-weight: 700;
    color: var(--brand-text);
    line-height: 1.2;
  }
  .holder-title {
    font-size: 23px;
    color: var(--grey-name);
    line-height: 1.2;
  }
  .contact {
    position: absolute;
    left: 380px;
    bottom: 52px;
    font-size: 21px;
    line-height: 1.45;
    color: var(--grey-text);
    list-style: none;
  }
  .edge-stripe {
    position: absolute;
    top: 0;
    right: 0;
    width: 22px;
    height: 100%;
    background: linear-gradient(180deg, var(--stripe-light), var(--stripe-dark));
  }
</style>
</head>
<body>
  <main class="canvas">
    <section class="card card-back" aria-label="Card back">
      <div class="brand">
        <span class="brand-mark" aria-hidden="true"></span>
        <span class="brand-name">VOLTINA PARTNERS</span>
      </div>
      <p class="website">www.voltinapartners.com.au</p>
    </section>

    <section class="card card-front" aria-label="Card front">
      <div class="brand">
        <span class="brand-mark" aria-hidden="true"></span>
        <span class="brand-name">VOLTINA PARTNERS</span>
      </div>
      <div class="holder">
        <p class="holder-name">Peter Welling</p>
        <p class="holder-title">Director</p>
      </div>
      <ul class="contact">
        <li>238 Morrow Tce, Kelvin Grove</li>
        <li>QLD 4059</li>
        <li>P: 07 3628 4190</li>
        <li>M: 0418 527 306</li>
        <li>peter@voltinapartners.com.au</li>
      </ul>
      <div class="edge-stripe" aria-hidden="true"></div>
    </section>
  </main>
</body>
</html>
```